Computer consultant business card

Qorvane Software is a newly started computer consulting company. It's a small one-man company that provides mostly Vornix applications but also websites in collaboration with designers. I'm running this company on the side of full time university studies.

I want the final design to be clean and memorable. Be creative! :)

Some inspiration:
http://www.pixelmarta.com/design/48317
http://www.pixelmarta.com/design/2739164/business-card-design-by-frostlynk
http://www.pixelmarta.com/design/604281/business-card-design-by-koralind-vestrabanu

See attachment for my company logo.
Updates

I would like to thank everyone for submitting! I'll need a couple of days to review and ultimately select a design.

Target Market(s)

Non-technical entrepreneurs and small companies.

Industry/Entity Type

University

Requirements
Must have
• My company logo.
In any way, both colors from my logo.
First- and last name, e-mail and phone number.
Double-sided design.
Nice to have
• Something creative with the symbol in my logo

```html
<!DOCTYPE html>
<html lang="en">
<head>
<meta charset="utf-8">
<title>Qorvane Software – Business Card</title>
<link href="https://fonts.googleapis.com/css2?family=Open+Sans:wght@400;600;700&display=swap" rel="stylesheet">
<style>
  :root {
    --page-bg: #e9e6e1;
    --card-black: #0d0d0e;
    --card-charcoal: #1c1c1e;
    --pattern-tone: #2a2a2c;
    --brand-grey: #8f9092;
    --brand-blue: #3b6fc6;
    --text-white: #f2f2f2;
    --rule-grey: #6a6a6c;
  }
  * { margin: 0; padding: 0; box-sizing: border-box; }
  html, body {
    width: 1200px; height: 900px; overflow: hidden;
    background: var(--page-bg);
    font-family: "Open Sans", Arial, sans-serif;
  }
  .stage {
    width: 1200px; height: 900px;
    display: flex; justify-content: center; align-items: center; gap: 80px;
  }
  .card {
    position: relative;
    width: 360px; height: 620px;
    border-radius: 30px;
    overflow: hidden;
    background: linear-gradient(160deg, var(--card-charcoal) 0%, var(--card-black) 55%, #050505 100%);
    box-shadow: 0 14px 30px rgba(0,0,0,.28);
  }
  .card__pattern {
    position: absolute; inset: 0;
    background:
      radial-gradient(ellipse at 50% 40%, rgba(60,60,64,.55) 0%, rgba(30,30,32,.25) 55%, rgba(0,0,0,0) 80%),
      linear-gradient(180deg, var(--pattern-tone) 0%, rgba(20,20,22,.4) 100%);
    opacity: .7;
  }
  .card--front .card__pattern { bottom: 240px; }

  .brand {
    position: absolute;
    display: flex; align-items: center;
    color: var(--brand-grey);
    font-weight: 700;
    white-space: nowrap;
  }
  .brand__dot {
    flex: none;
    border-radius: 50%;
    background: var(--brand-blue);
  }
  .card--front .brand { top: 160px; left: 34px; gap: 14px; font-size: 46px; }
  .card--front .brand__dot { width: 56px; height: 56px; }
  .card--back .brand { top: 270px; left: 0; right: 0; justify-content: center; font-size: 70px; }

  .contact {
    position: absolute; left: 60px; right: 30px; top: 380px;
    color: var(--text-white);
  }
  .contact__rule {
    height: 1px;
    background: linear-gradient(90deg, rgba(0,0,0,0), var(--rule-grey) 40%, #bbb 70%, rgba(0,0,0,0));
  }
  .contact__name {
    margin-top: 10px;
    color: var(--brand-blue);
    font-size: 25px; font-weight: 700; line-height: 1.1;
  }
  .contact__title {
    font-size: 18px; margin: 2px 0 12px 64px;
  }
  .contact__address {
    margin-top: 14px;
    font-size: 15px; line-height: 1.3;
  }
  .contact__line {
    display: flex; align-items: center; gap: 10px;
    font-size: 15px; margin-top: 6px;
  }
  .contact__line svg { flex: none; }
</style>
</head>
<body>
<main class="stage">

  <section class="card card--front">
    <div class="card__pattern" role="img" aria-label="Faint repeating pattern of the brand symbol across the card"></div>
    <div class="brand"><span class="brand__dot"></span>qorvane</div>
    <div class="contact">
      <div class="contact__rule"></div>
      <p class="contact__name">Your Name</p>
      <p class="contact__title">Job Title</p>
      <div class="contact__rule"></div>
      <p class="contact__address">your address goes here,<br>State,City, Zip Code</p>
      <p class="contact__line">
        <svg width="10" height="16" viewBox="0 0 10 16"><rect x="1" y="1" width="8" height="14" rx="1.5" fill="none" stroke="var(--brand-blue)" stroke-width="1.6"/></svg>
        000-000-000
      </p>
      <p class="contact__line">
        <svg width="14" height="10" viewBox="0 0 14 10"><rect width="14" height="10" rx="1" fill="var(--brand-blue)"/><path d="M0 0 L7 5 L14 0" fill="none" stroke="var(--card-black)" stroke-width="1"/></svg>
        name@domainname.com
      </p>
    </div>
  </section>

  <section class="card card--back">
    <div class="card__pattern" role="img" aria-label="Faint repeating pattern of the brand symbol across the card"></div>
    <div class="brand">qorvane</div>
  </section>

</main>
</body>
</html>
```